Simplified minimalist but bold website

Design a website for a brand 'Brighten Every Day' that shares ideas to make managing home and health easier through email swap series, webinars and eventually courses.

Simple landing page to attract users to sign up for a freebie.

Target Market(s)

women with families & homes to run

Number of Pages Required

1 page

Font styles to use
Sans Serif

Colors
e667a6
b768aa
acd136
ffffff
959595

Requirements
Must have
• Simplified look, line icons, opt-in template, contact us form

```html
<!DOCTYPE html>
<html lang="en">
<head>
<meta charset="utf-8">
<title>Brighten Every Day</title>
<link href="https://fonts.googleapis.com/css2?family=Montserrat:wght@500;600;700&family=Open+Sans:wght@400;600&display=swap" rel="stylesheet">
<style>
:root{
  --blue:#2e97d0;
  --pink:#e04d97;
  --green:#9dc92c;
  --ink:#222;
  --grey:#555;
  --white:#fff;
  --footer:#333;
}
*{box-sizing:border-box;margin:0;padding:0}
html,body{width:733px;height:1200px;overflow:hidden;background:var(--white)}
body{position:relative;font-family:"Open Sans",Arial,sans-serif;color:var(--ink)}
.abs{position:absolute}
.center{left:0;right:0;text-align:center}
.topline{top:0;left:0;width:733px;height:3px;background:var(--pink)}
.menu-btn{top:0;left:682px;width:51px;height:41px;background:var(--pink)}
.menu-btn span{position:absolute;left:16px;width:20px;height:2.5px;background:var(--white);border-radius:2px}
.hero{top:3px;left:0;width:733px;height:413px;background:linear-gradient(180deg,#f4f4f4 0%,#ececec 70%,#dedede 100%)}
.hero-people{top:175px;left:250px;width:300px;height:241px;background:radial-gradient(ellipse at 50% 55%,#8da0b8 0%,#b8c1cc 45%,rgba(230,230,230,0) 75%)}
.brand-title{top:58px;font-family:Montserrat,Arial,sans-serif;font-weight:700;font-size:30px;letter-spacing:2px;color:var(--blue)}
.rule{height:1.5px;width:46px;background:var(--ink);left:50%;margin-left:-23px}
.rule.light{background:var(--white)}
.hero-sub{top:122px;font-family:Montserrat,Arial,sans-serif;font-weight:500;font-size:16px;line-height:23px}
.panel{top:416px;width:366.5px;height:384px;color:var(--white);text-align:center}
.panel.swaps{left:0;background:var(--blue)}
.panel.guide{left:366.5px;background:var(--pink)}
.panel .eyebrow{position:absolute;top:23px;left:0;right:0;font-family:Montserrat,Arial,sans-serif;font-size:9.5px;letter-spacing:.8px}
.panel h2{position:absolute;top:60px;left:0;right:0;font-family:Montserrat,Arial,sans-serif;font-weight:600;font-size:17px;letter-spacing:1.5px}
.panel .rule{top:94px}
.panel .lead{position:absolute;top:109px;left:0;right:0;font-family:Montserrat,Arial,sans-serif;font-weight:600;font-size:11px;line-height:15px}
.panel .body{position:absolute;top:147px;left:0;right:0;font-size:8.5px;line-height:15.5px}
.panel .links{position:absolute;top:207px;left:0;right:0;font-family:Montserrat,Arial,sans-serif;font-weight:600;font-size:8.5px}
.panel .links a{color:var(--white);margin:0 9px;text-decoration:underline}
.panel .ask{position:absolute;top:240px;left:0;right:0;font-family:Montserrat,Arial,sans-serif;font-weight:600;font-size:11.5px}
.field{position:absolute;left:68px;width:227px;height:27px;background:var(--white);color:#999;font-size:8px;text-align:left;padding:8px 10px}
.field svg{position:absolute;right:9px;top:9px}
.f1{top:262px}.f2{top:292px}
.cta{position:absolute;left:68px;top:323px;width:227px;height:27px;font-family:Montserrat,Arial,sans-serif;font-weight:600;font-size:8.5px;line-height:27px;color:var(--white);letter-spacing:.3px}
.swaps .cta{background:var(--pink)}
.guide .cta{background:var(--blue)}
.guide-art{position:absolute;top:109px;left:78px;width:194px;height:143px;background:linear-gradient(135deg,#f6f6f6,#dcdcdc)}
.detail{top:800px;left:0;width:733px;height:354px;background:linear-gradient(135deg,#f7f7f5 0%,#ecebe8 50%,#f3f3f1 100%)}
.detail-title{top:842px;font-family:Montserrat,Arial,sans-serif;font-weight:600;font-size:24px;letter-spacing:1.8px;color:var(--green)}
.detail .rule{top:81px}
.detail-copy{top:898px;font-size:9.5px;line-height:18.4px;color:var(--grey)}
.detail-join{top:1041px;font-family:Montserrat,Arial,sans-serif;font-weight:500;font-size:9.5px;line-height:18px;color:var(--grey)}
.detail-cta{top:1089px;left:253px;width:227px;height:27px;background:var(--green);color:var(--white);text-align:center;font-family:Montserrat,Arial,sans-serif;font-weight:600;font-size:8.5px;line-height:27px}
.footer{top:1154px;left:0;width:733px;height:46px;background:var(--footer);color:var(--white)}
.footer .legal{position:absolute;left:67px;top:18px;font-family:Montserrat,Arial,sans-serif;font-size:8px}
.footer .social{position:absolute;right:70px;top:17px;display:flex;gap:10px}
.footer .social span{width:11px;height:11px;border-radius:50%;background:var(--white)}
</style>
</head>
<body>
<div class="abs hero" role="img" aria-label="Bright room with a smiling couple sitting on the floor and simple sketched furniture"></div>
<div class="abs hero-people" role="img" aria-label="Couple sitting together against the wall"></div>
<div class="abs topline"></div>
<div class="abs menu-btn"><span style="top:14px"></span><span style="top:19.5px"></span><span style="top:25px"></span></div>
<h1 class="abs center brand-title">Brighten Every Day.</h1>
<div class="abs rule" style="top:104px"></div>
<p class="abs center hero-sub">Chances are life is a little overwhelming.<br>Let us help</p>
<svg class="abs" style="top:360px;left:356px" width="22" height="14" viewBox="0 0 22 14"><path d="M1 2l10 10 10-10" fill="none" stroke="#fff" stroke-width="1.2"/><path d="M5 1l6 6 6-6" fill="none" stroke="#fff" stroke-width="1"/></svg>

<section class="abs panel swaps">
  <p class="eyebrow">Baby Steps... (try out a few of our tricks)</p>
  <h2>Swaps Email Series</h2>
  <div class="rule light abs"></div>
  <p class="lead">Save TIME, MONEY and SANITY<br>with simple product swaps.</p>
  <p class="body">Reduce the amount of work it takes to run your home.<br>Swap out existing products for more sustainable ones.<br>Each swap saves you work, clutter, time &amp; money.</p>
  <p class="links"><a href="#">SEE SAMPLE SWAP</a><a href="#">LEARN MORE</a></p>
  <p class="ask">Send your ideas my way..</p>
  <div class="field f1">Name<svg width="7" height="8" viewBox="0 0 7 8"><circle cx="3.5" cy="2" r="2" fill="#888"/><path d="M0 8c0-3 7-3 7 0z" fill="#888"/></svg></div>
  <div class="field f2">Email:<svg width="9" height="7" viewBox="0 0 9 7"><rect width="9" height="7" fill="#888"/><path d="M0 0l4.5 4L9 0" fill="none" stroke="#fff" stroke-width=".8"/></svg></div>
  <div class="cta">SEND ME THE GUIDE!</div>
</section>

<section class="abs panel guide">
  <p class="eyebrow">Big Leap... (I'm ready to roll up my sleeves)</p>
  <h2>Decluttering Guide</h2>
  <div class="rule light abs"></div>
  <div class="guide-art" role="img" aria-label="Two printed guide pages fanned out"></div>
  <div class="field f1">Name<svg width="7" height="8" viewBox="0 0 7 8"><circle cx="3.5" cy="2" r="2" fill="#888"/><path d="M0 8c0-3 7-3 7 0z" fill="#888"/></svg></div>
  <div class="field f2">Email:<svg width="9" height="7" viewBox="0 0 9 7"><rect width="9" height="7" fill="#888"/><path d="M0 0l4.5 4L9 0" fill="none" stroke="#fff" stroke-width=".8"/></svg></div>
  <div class="cta">SIGN ME UP!</div>
</section>

<section class="abs detail" role="img" aria-label="Faded photo of a couple relaxing on the floor of a bright room with moving boxes">
  <div class="rule abs"></div>
</section>
<h2 class="abs center detail-title">Swaps Email Series</h2>
<p class="abs center detail-copy">Save TIME, MONEY and SANITY with simple product swaps.<br>And reduce the amount of work it takes to run your home.<br>Swap out existing products for more sustainable ones.<br>Each swap save you work, clutter, time &amp; money.<br><br>You get an email &nbsp;2x weekly for 6-12 weeks only<br>Get even more if you feel they are helpful to you</p>
<p class="abs center detail-join">Join our monthly SIMPLE SWAP SHARING web jams with other mums and get even<br>more ideas. Better yet, come with great tips of your own to share.</p>
<div class="abs detail-cta">SIGN ME UP!</div>

<footer class="abs footer">
  <p class="legal">© 2018 All Rights Are Reserved.Terms of Use | Privacy Policy</p>
  <div class="social"><span></span><span></span><span></span><span></span></div>
</footer>
</body>
</html>
```